Business Card Design

We provide services doing multiple jobs in the construction industry.Please note: The company name needs to be ROCK SOLID BUILDING SERVICESAttached logo was an example of what we wanted. Can you change up the colors?

Industry/Entity Type

Construction

Contact Information for Business Card

ROCK SOLID BUILDING SERVICES5401 HUDSON BEND RDAUSTIN, TX 78734(512)243-6854ROCKSOLIDBUILDINGSERVICES@GMAIL.COM

```html
<!DOCTYPE html>
<html lang="en">
<head>
<meta charset="utf-8">
<title>Pearlwood Framing Works — Business Card</title>
<link href="https://fonts.googleapis.com/css2?family=Michroma&display=swap" rel="stylesheet">
<style>
  :root {
    --backdrop: #9a9d9c;
    --navy-light: #34338c;
    --navy-dark: #1c1b57;
    --charcoal: #3a3b40;
    --silver: #b9bbc1;
    --paper: #ffffff;
    --cream: #f3ecd6;
    --ink-on-navy: #e9e9f3;
    --ink-navy: #232266;
  }
  html, body {
    margin: 0;
    width: 1200px;
    height: 807px;
    overflow: hidden;
    background: var(--backdrop);
    font-family: "Michroma", sans-serif;
  }
  .sheet {
    position: relative;
    width: 1200px;
    height: 807px;
    display: flex;
    align-items: center;
    justify-content: center;
    gap: 48px;
  }
  .card {
    position: relative;
    width: 532px;
    height: 304px;
    overflow: hidden;
    box-shadow: 0 6px 18px rgba(0,0,0,.25);
  }
  /* Front */
  .card--front {
    background: radial-gradient(ellipse at 62% 35%, var(--navy-light), var(--navy-dark) 80%);
  }
  .card__swoosh {
    position: absolute;
    inset: 0;
    width: 100%;
    height: 100%;
  }
  .brand {
    position: absolute;
    top: 56px;
    left: 200px;
    width: 300px;
    display: flex;
    align-items: center;
    gap: 12px;
    color: var(--cream);
    font-size: 17px;
    line-height: 1.35;
    letter-spacing: .5px;
  }
  .brand__mark {
    flex: none;
    width: 26px;
    height: 26px;
    background: var(--cream);
  }
  .person {
    position: absolute;
    top: 148px;
    right: 284px;
    text-align: right;
    color: var(--ink-on-navy);
    font-size: 9px;
    line-height: 1.55;
    letter-spacing: .6px;
  }
  .person__name { font-size: 10.5px; letter-spacing: 1.2px; }
  .person__address { margin-top: 10px; }
  .divider {
    position: absolute;
    top: 148px;
    left: 260px;
    width: 1px;
    height: 78px;
    background: var(--ink-on-navy);
    opacity: .8;
  }
  .contacts {
    position: absolute;
    top: 146px;
    left: 272px;
    margin: 0;
    padding: 0;
    list-style: none;
    color: var(--ink-on-navy);
    font-size: 9px;
    letter-spacing: .6px;
  }
  .contacts li {
    display: flex;
    align-items: center;
    gap: 6px;
    height: 16px;
  }
  .contacts svg { width: 11px; height: 11px; flex: none; }
  /* Back */
  .card--back { background: var(--paper); }
  .brand--back {
    top: 112px;
    left: 96px;
    width: 360px;
    color: var(--ink-navy);
    font-size: 24px;
  }
  .brand--back .brand__mark { width: 34px; height: 34px; background: var(--ink-navy); }
</style>
</head>
<body>
<main class="sheet">
  <section class="card card--front" aria-label="Card front">
    <svg class="card__swoosh" viewBox="0 0 532 304" preserveAspectRatio="none" aria-hidden="true">
      <path d="M0 130 C 60 260, 250 300, 532 275 L532 304 L0 304 Z" fill="var(--silver)"/>
      <path d="M0 142 C 60 270, 250 304, 532 287 L532 304 L0 304 Z" fill="var(--charcoal)"/>
      <path d="M0 124 C 60 254, 250 294, 532 270 L532 274 C 250 299, 60 260, 0 131 Z" fill="var(--paper)" opacity=".5"/>
    </svg>

    <div class="brand">
      <span class="brand__mark"></span>
      <span class="brand__name">PEARLWOOD FRAMING WORKS</span>
    </div>

    <div class="person">
      <div class="person__name">DANA WHITLOW</div>
      <div class="person__title">Owner / C.E.O</div>
      <div class="person__address">Unit 14, Fernglen Yard,<br>TX 78734</div>
    </div>

    <div class="divider"></div>

    <ul class="contacts">
      <li><svg viewBox="0 0 12 12"><circle cx="6" cy="6" r="6" fill="#e9e9f3"/><path d="M3.6 3.2l1.2-.4.7 1.6-.8.5a4 4 0 0 0 1.9 1.9l.5-.8 1.6.7-.4 1.2C6.1 8.5 3.5 5.9 3.6 3.2z" fill="#1c1b57"/></svg>(512)555-0193</li>
      <li><svg viewBox="0 0 12 12"><circle cx="6" cy="6" r="6" fill="#e9e9f3"/><rect x="4" y="2.5" width="4" height="7" rx=".8" fill="#1c1b57"/></svg>(512)555-0147</li>
      <li><svg viewBox="0 0 12 12"><circle cx="6" cy="6" r="6" fill="#e9e9f3"/><rect x="3" y="5" width="6" height="3.5" fill="#1c1b57"/><rect x="4" y="3" width="4" height="2" fill="#1c1b57"/></svg>(512)555-0162</li>
      <li><svg viewBox="0 0 12 12"><circle cx="6" cy="6" r="6" fill="#e9e9f3"/><rect x="3" y="4" width="6" height="4.2" fill="#1c1b57"/><path d="M3 4l3 2.3L9 4" stroke="#e9e9f3" stroke-width=".7" fill="none"/></svg>office@pearlwood.example</li>
      <li><svg viewBox="0 0 12 12"><circle cx="6" cy="6" r="6" fill="#e9e9f3"/><circle cx="6" cy="6" r="3.2" fill="none" stroke="#1c1b57" stroke-width=".8"/><path d="M2.8 6h6.4M6 2.8v6.4" stroke="#1c1b57" stroke-width=".7"/></svg>www.pearlwood.example</li>
    </ul>
  </section>

  <section class="card card--back" aria-label="Card back">
    <div class="brand brand--back">
      <span class="brand__mark"></span>
      <span class="brand__name">PEARLWOOD FRAMING WORKS</span>
    </div>
  </section>
</main>
</body>
</html>
```